5KO Outings

Explain what 5KO means ( Water, Wave, Wake Expereince)
We offer surfing, wake baording, water skliing on a state of the art surf and equipment all included in the charter. The captain is a Norvane Shore Watch captain.
We offer wake surfing, wakeboarding, water skiing, tubing. We have state of the art video with 3 cameras onboard 2,360 view camers for videioing your day on the water.
Located on the Delta, serving Lake Tahoe in the summer time, Lake Berryasea, and other local lakes.
We specliaize in birthday parties, bacholer, bachlorrete, graduation parties and team building events.

Target Market(s)

Indivuals, business, wedding and event planners

Industry/Entity Type

Water sports

Requirements
Must have
• My logo,
Nice to have
• Simple, not to busy

```html
<!DOCTYPE html>
<html lang="en">
<head>
<meta charset="utf-8">
<title>5KO Outings – Ride the Waves</title>
<link rel="stylesheet" href="https://fonts.googleapis.com/css2?family=Poppins:ital,wght@0,400;0,500;0,600;0,700;0,800;1,800&family=Dancing+Script:wght@600&display=swap">
<style>
  :root{
    --page-bg:#d3d3d3;
    --navy:#0b2455;
    --navy-deep:#081c45;
    --royal:#0c3f94;
    --sky-blue:#2bb3f0;
    --gold:#f2b705;
    --gold-box:#dba800;
    --red:#c4112f;
    --red-dark:#8e0a1f;
    --white:#ffffff;
  }
  *{box-sizing:border-box;margin:0;padding:0}
  html,body{width:1200px;height:1200px;overflow:hidden;background:var(--page-bg)}
  body{font-family:'Poppins',sans-serif;color:var(--white);position:relative}
  .flyer{position:absolute;left:150px;top:18px;width:900px;height:1165px;overflow:hidden;background:var(--white)}
  .scene-photo{position:absolute;left:0;top:0;width:100%;height:100%;
    background:linear-gradient(180deg,#ffffff 0%,#e6f0f9 6%,#c3dbf0 30%,#9cc1e2 48%,#4f7a8a 52%,#3c6fa6 56%,#1f63b9 66%,#0f55b4 85%,#0b4aa6 100%)}
  .hero-panel{position:absolute;left:71px;top:41px;width:746px;height:530px;border-radius:34px 34px 0 0;
    background:linear-gradient(180deg,var(--royal) 0%,#114fa6 60%,rgba(30,100,190,0.35) 100%)}
  .brand{position:absolute;left:0;top:78px;width:100%;text-align:center}
  .brand-name{display:inline-flex;align-items:center;gap:8px;font-weight:700;font-size:26px;letter-spacing:1px}
  .brand-dot{width:16px;height:16px;border-radius:50%;background:var(--white)}
  .tagline{position:absolute;left:0;top:146px;width:100%;text-align:center;font-weight:600;font-size:12px;letter-spacing:.4px}
  .headline{position:absolute;left:0;top:166px;width:100%;text-align:center;font-weight:700;font-size:62px;line-height:1;letter-spacing:-.5px}
  .headline .accent{color:var(--sky-blue)}
  .headline-sub{position:absolute;left:0;top:228px;width:100%;text-align:center;font-weight:700;font-size:62px;line-height:1.05}
  .headline-sub .script{font-family:'Dancing Script',cursive;font-weight:600;font-size:40px;margin-right:6px}
  .rule{position:absolute;left:160px;top:302px;width:580px;height:1px;background:rgba(255,255,255,.8)}
  .pillars{position:absolute;left:0;top:312px;width:100%;display:flex;justify-content:center;gap:24px;font-size:31px;font-weight:400}
  .pillars span{display:inline-flex;align-items:center;gap:6px}
  .tick{width:15px;height:15px}
  .adventure-card{position:absolute;left:415px;top:375px;width:350px;height:170px;background:var(--navy-deep);border-radius:12px 12px 0 0;padding:22px 0 0 38px}
  .adventure-card .line1{font-size:32px;font-weight:500;line-height:1.1}
  .adventure-card .line2{font-size:39px;font-weight:800;font-style:italic;color:var(--gold);line-height:1.1}
  .adventure-card .line3{font-size:24px;font-weight:400;letter-spacing:5px;margin-top:4px}
  .badge{position:absolute;left:658px;top:515px;width:176px;height:176px}
  .badge-text{position:absolute;left:658px;top:515px;width:176px;height:176px;display:flex;align-items:center;justify-content:center;text-align:center;font-weight:700;font-size:16px;line-height:1.35}
  .snapshot{position:absolute;background:var(--white);padding:8px;box-shadow:0 4px 10px rgba(0,0,0,.3)}
  .snapshot div{width:100%;height:100%}
  .snapshot.one{left:62px;top:690px;width:165px;height:158px;transform:rotate(-9deg)}
  .snapshot.one div{background:linear-gradient(180deg,#f2f4f4 0%,#cfd9de 50%,#8a9aa3 100%)}
  .snapshot.two{left:215px;top:760px;width:158px;height:165px;transform:rotate(9deg)}
  .snapshot.two div{background:linear-gradient(180deg,#6f8a3c 0%,#8aa25a 45%,#b8b49a 75%,#9a9a8c 100%)}
  .offer-title{position:absolute;left:76px;top:870px;font-size:23px;line-height:1.2}
  .offer-title b{font-weight:700}
  .services{position:absolute;left:80px;top:945px;width:262px}
  .service{position:relative;height:34px;margin-bottom:6px;border-radius:5px;padding-left:25px;font-weight:700;font-size:19px;line-height:34px}
  .service.gold{background:var(--gold-box)}
  .service.navy{background:var(--navy)}
  .service .dot{position:absolute;left:-8px;top:10px;width:14px;height:14px}
  .features{position:absolute;left:430px;top:694px;width:401px}
  .feature{position:relative;height:84px;margin-bottom:9px;border-radius:6px;padding:12px 50px 0 30px}
  .feature.navy{background:var(--navy)}
  .feature.gold{background:var(--gold-box)}
  .feature h3{font-size:20px;font-weight:700;line-height:1.15;white-space:nowrap}
  .feature.navy h3{color:var(--gold)}
  .feature.gold h3{color:var(--navy-deep)}
  .feature p{font-size:12px;font-weight:600;line-height:1.3;margin-top:3px}
  .feature.gold p{color:var(--navy-deep)}
  .feature-icon{position:absolute;left:-21px;top:24px;width:36px;height:36px;border-radius:50%;background:var(--white);border:3px solid var(--royal);display:flex;align-items:center;justify-content:center}
  .feature-icon svg{width:20px;height:20px}
  .cta{position:absolute;left:75px;top:1074px}
  .cta .big{font-size:31px;font-weight:800;line-height:1}
  .cta .small{font-size:19px;font-weight:700;color:var(--gold);line-height:1.3}
  .cta-divider{position:absolute;left:300px;top:1078px;width:1px;height:46px;background:rgba(255,255,255,.8)}
  .contact{position:absolute;left:350px;top:1074px;font-weight:600;font-size:21px}
  .contact-row{display:flex;align-items:center;gap:8px;height:28px}
  .contact-row svg{width:17px;height:17px}
  .contact .mail-icon{margin-left:18px}
  .contact .email{font-weight:500}
  .contact .web{font-weight:700;letter-spacing:8px;font-size:21px}
</style>
</head>
<body>
<div class="flyer">
  <div class="scene-photo" role="img" aria-label="Photo of a wake surfer in a wetsuit riding behind a boat on a lake, with a second rider on a cresting wave, green hills and cloudy blue sky"></div>

  <div class="hero-panel"></div>

  <div class="brand"><span class="brand-name"><span class="brand-dot"></span>5KO Outings</span></div>
  <div class="tagline">GLIDE IT, JUMP IT, FLOW IT!</div>
  <h1 class="headline">RIDE THE <span class="accent">WAVES</span></h1>
  <div class="headline-sub"><span class="script">with</span>5KO!</div>
  <div class="rule"></div>

  <div class="pillars">
    <span><svg class="tick" viewBox="0 0 16 16"><circle cx="8" cy="8" r="8" fill="#f2b705"/><path d="M4.5 8.2l2.3 2.3 4.6-4.8" stroke="#0c3f94" stroke-width="2" fill="none"/></svg>Water</span>
    <span><svg class="tick" viewBox="0 0 16 16"><circle cx="8" cy="8" r="8" fill="#f2b705"/><path d="M4.5 8.2l2.3 2.3 4.6-4.8" stroke="#0c3f94" stroke-width="2" fill="none"/></svg>Wave</span>
    <span><svg class="tick" viewBox="0 0 16 16"><circle cx="8" cy="8" r="8" fill="#f2b705"/><path d="M4.5 8.2l2.3 2.3 4.6-4.8" stroke="#0c3f94" stroke-width="2" fill="none"/></svg>Wake Experience</span>
  </div>

  <div class="adventure-card">
    <div class="line1">Unforgettable</div>
    <div class="line2">ADVENTURES</div>
    <div class="line3">ON THE WATER!</div>
  </div>

  <svg class="badge" viewBox="0 0 180 180" aria-hidden="true">
    <polygon fill="var(--red-dark)" points="178,90 163.4,109.7 166.2,134 143.7,143.7 134,166.2 109.7,163.4 90,178 70.3,163.4 46,166.2 36.3,143.7 13.8,134 16.6,109.7 2,90 16.6,70.3 13.8,46 36.3,36.3 46,13.8 70.3,16.6 90,2 109.7,16.6 134,13.8 143.7,36.3 166.2,46 163.4,70.3"/>
    <circle cx="90" cy="90" r="72" fill="var(--red)"/>
  </svg>
  <div class="badge-text">All<br>equipment<br>included<br>in the<br>charter!</div>

  <div class="snapshot one"><div role="img" aria-label="Photo of a windsurfer on a bright lake"></div></div>
  <div class="snapshot two"><div role="img" aria-label="Photo of a rider on a board in a tree-lined river"></div></div>

  <div class="offer-title">What<br><b>We Offer</b></div>
  <div class="services">
    <div class="service gold"><svg class="dot" viewBox="0 0 16 16"><circle cx="8" cy="8" r="8" fill="#fff"/><circle cx="8" cy="8" r="6" fill="#1a6fd8"/><path d="M5 8.2l2 2 4-4.2" stroke="#fff" stroke-width="1.8" fill="none"/></svg>Wake Surfing</div>
    <div class="service navy"><svg class="dot" viewBox="0 0 16 16"><circle cx="8" cy="8" r="8" fill="#fff"/><circle cx="8" cy="8" r="6" fill="#1a6fd8"/><path d="M5 8.2l2 2 4-4.2" stroke="#fff" stroke-width="1.8" fill="none"/></svg>Wakeboarding</div>
    <div class="service gold"><svg class="dot" viewBox="0 0 16 16"><circle cx="8" cy="8" r="8" fill="#fff"/><circle cx="8" cy="8" r="6" fill="#1a6fd8"/><path d="M5 8.2l2 2 4-4.2" stroke="#fff" stroke-width="1.8" fill="none"/></svg>Water Skiing &amp; Tubing</div>
  </div>

  <div class="features">
    <div class="feature navy">
      <div class="feature-icon"><svg viewBox="0 0 24 24" fill="none" stroke="#0c3f94" stroke-width="1.6"><path d="M6 8h12l-1-3H7z"/><circle cx="12" cy="11" r="3"/><path d="M5 21v-3a5 5 0 0 1 14 0v3z"/></svg></div>
      <h3>Expert Captain</h3>
      <p>Led by a Norvane Shore Watch-certified pro for a safe and thrilling ride.</p>
    </div>
    <div class="feature gold">
      <div class="feature-icon"><svg viewBox="0 0 24 24" fill="none" stroke="#0c3f94" stroke-width="1.8"><rect x="3" y="7" width="12" height="10" rx="2"/><path d="M15 11l6-3v8l-6-3z"/></svg></div>
      <h3>Pro-Level Video Recording</h3>
      <p>3 onboard cameras, including two 360° view camera, to capture every epic moment.</p>
    </div>
    <div class="feature navy">
      <div class="feature-icon"><svg viewBox="0 0 24 24" fill="none" stroke="#0c3f94" stroke-width="1.8"><path d="M12 22s-7-7-7-12a7 7 0 0 1 14 0c0 5-7 12-7 12z"/><circle cx="12" cy="10" r="2.5"/></svg></div>
      <h3>Prime Locations</h3>
      <p>Based on the Delta, serving Lake Tahoe (summer), Lake Berryessa, and other local lakes.</p>
    </div>
    <div class="feature gold">
      <div class="feature-icon"><svg viewBox="0 0 24 24" fill="none" stroke="#0c3f94" stroke-width="1.8"><rect x="3" y="5" width="18" height="16" rx="2"/><path d="M8 3v4M16 3v4M3 10h18"/><path d="M12 12.5l1.2 2.3 2.5.3-1.8 1.7.5 2.5-2.4-1.2-2.4 1.2.5-2.5-1.8-1.7 2.5-.3z"/></svg></div>
      <h3>Perfect for Special Events</h3>
      <p>Birthday parties, bachelor/bachelorette parties, graduations, and team-building events.</p>
    </div>
  </div>

  <div class="cta">
    <div class="big">BOOK YOUR</div>
    <div class="small">ADVENTURE TODAY!</div>
  </div>
  <div class="cta-divider"></div>

  <div class="contact">
    <div class="contact-row">
      <svg viewBox="0 0 24 24" fill="none" stroke="#f2b705" stroke-width="2"><path d="M5 3h4l2 5-2.5 1.5a11 11 0 0 0 6 6L16 13l5 2v4a2 2 0 0 1-2 2A16 16 0 0 1 3 5a2 2 0 0 1 2-2z"/></svg>
      <span>012.555.0148</span>
      <svg class="mail-icon" viewBox="0 0 24 24" fill="#f2b705"><path d="M2 5h20v14H2z"/><path d="M2 5l10 8 10-8" stroke="#0f55b4" stroke-width="1.6" fill="none"/></svg>
      <span class="email">hello@5kooutings.com</span>
    </div>
    <div class="contact-row">
      <svg viewBox="0 0 24 24" fill="none" stroke="#f2b705" stroke-width="2"><circle cx="12" cy="12" r="9"/><path d="M3 12h18M12 3c3 3 3 15 0 18M12 3c-3 3-3 15 0 18"/></svg>
      <span class="web">www.5kooutings.com</span>
    </div>
  </div>
</div>
</body>
</html>
```